The Velvet Magpie business card

I need a business card for my makeup artist business. I specialise in bridal, glamour, formal and special occasion makeup.
I am a mobile makeup artist who caters for every from nowra to sydney.
I do the following services:
Bridal makeup
airbrush makeup
special occasion
formals
hens nights/ girls night
makeup lesson
makeup for all ages from flower girl to Nanna of the bride!
photoshoot makeup
SPFX

I would like the card to portray a very professional sleek makeup business. I would also like another version of the card directed especially towards brides.

Please see my website to understand colours etc www.thevelvetmagpie-example.com

The Velvet Magpie
Professional Makeup Artist
Lorraine Kedby
0491802643
info@thevelvetmagpie-example.com
www.thevelvetmagpie-example.com
www.facebook.com/thevelvetmagpie

```html
<!DOCTYPE html>
<html lang="en">
<head>
<meta charset="utf-8">
<title>The Velvet Magpie – Business Card</title>
<link rel="stylesheet" href="https://fonts.googleapis.com/css2?family=Josefin+Sans:wght@300&family=Roboto+Condensed:wght@400;700&display=swap">
<style>
  :root {
    --pink: #e0157f;
    --grey: #5b5b5b;
    --grey-light: #a9a9a9;
    --ink: #2b2b2b;
    --paper: #ffffff;
    --backdrop: #ecebe8;
  }
  * { box-sizing: border-box; margin: 0; padding: 0; }
  html, body { width: 1200px; height: 913px; overflow: hidden; }
  body {
    background: var(--backdrop);
    font-family: "Roboto Condensed", Arial, sans-serif;
    position: relative;
  }
  .card {
    position: absolute;
    width: 540px;
    height: 330px;
    background: var(--paper);
    border-radius: 18px;
    overflow: hidden;
    box-shadow: 0 6px 18px rgba(0,0,0,.18);
  }
  .card--front { left: 40px; top: 292px; }
  .card--back { left: 620px; top: 292px; }
  .card__art { position: absolute; inset: 0; width: 100%; height: 100%; }

  .brand {
    position: absolute;
    left: 34px;
    top: 62px;
    font-family: "Josefin Sans", Arial, sans-serif;
    font-weight: 300;
    font-size: 28px;
    letter-spacing: 2px;
    white-space: nowrap;
    text-transform: uppercase;
    color: var(--pink);
  }
  .contacts {
    position: absolute;
    left: 36px;
    top: 160px;
    list-style: none;
  }
  .contacts li {
    display: flex;
    align-items: center;
    gap: 9px;
    height: 26px;
    font-size: 15px;
    white-space: nowrap;
    color: var(--ink);
  }
  .contacts svg { width: 15px; height: 15px; flex: none; }
  .contacts .marker {
    width: 13px; height: 13px; flex: none;
    background: var(--pink); border-radius: 2px; margin: 0 1px;
  }
  .artist {
    position: absolute;
    right: 18px;
    top: 218px;
    text-align: right;
    white-space: nowrap;
    color: var(--paper);
  }
  .artist__name { font-weight: 700; font-size: 20px; }
  .artist__title { font-size: 14px; margin-top: 2px; }

  .services {
    position: absolute;
    left: 18px;
    right: 18px;
    top: 228px;
    text-align: center;
    color: var(--pink);
    font-weight: 700;
    font-size: 16px;
    line-height: 1.45;
  }
</style>
</head>
<body>

<section class="card card--front" aria-label="Business card front">
  <svg class="card__art" viewBox="0 0 540 330" aria-hidden="true">
    <path d="M540 30 C 430 60, 400 250, 270 330 L540 330 Z" fill="var(--pink)"/>
    <path d="M540 16 C 420 46, 385 245, 240 330" fill="none" stroke="var(--grey)" stroke-width="8"/>
    <path d="M540 4 C 410 34, 370 240, 215 330" fill="none" stroke="var(--grey-light)" stroke-width="5"/>
    <path d="M540 46 C 440 76, 415 255, 295 330" fill="none" stroke="#ffffff" stroke-width="2.5" opacity=".7"/>
  </svg>

  <div class="brand">The Velvet Magpie</div>

  <ul class="contacts">
    <li>
      <svg viewBox="0 0 16 16"><path fill="var(--pink)" d="M3 2h3l1 3-2 1.2a8 8 0 0 0 4.8 4.8L11 9l3 1v3a1.5 1.5 0 0 1-1.5 1.5C7 14.5 1.5 9 1.5 3.5A1.5 1.5 0 0 1 3 2z"/></svg>
      0491802643
    </li>
    <li>
      <svg viewBox="0 0 16 16"><rect x="1" y="3" width="14" height="10" rx="1" fill="var(--pink)"/><path d="M1.5 3.5 8 9l6.5-5.5" fill="none" stroke="#fff" stroke-width="1.3"/></svg>
      info@thevelvetmagpie-example.com
    </li>
    <li>
      <svg viewBox="0 0 16 16"><circle cx="8" cy="8" r="7" fill="var(--pink)"/><path d="M1 8h14M8 1c-3 3-3 11 0 14M8 1c3 3 3 11 0 14" fill="none" stroke="#fff" stroke-width="1"/></svg>
      www.thevelvetmagpie-example.com
    </li>
    <li>
      <span class="marker"></span>
      /thevelvetmagpie
    </li>
  </ul>

  <div class="artist">
    <div class="artist__name">Lorraine Kedby</div>
    <div class="artist__title">Professional Makeup Artist</div>
  </div>
</section>

<section class="card card--back" aria-label="Business card back">
  <svg class="card__art" viewBox="0 0 540 330">
    <defs>
      <linearGradient id="tone-navy" x1="0" y1="0" x2="0" y2="1">
        <stop offset="0" stop-color="#3a3a42"/><stop offset="1" stop-color="#2a2f6e"/>
      </linearGradient>
      <linearGradient id="tone-skin" x1="0" y1="0" x2="1" y2="1">
        <stop offset="0" stop-color="#b9b178"/><stop offset="1" stop-color="#e9c3ab"/>
      </linearGradient>
      <linearGradient id="tone-party" x1="0" y1="0" x2="0" y2="1">
        <stop offset="0" stop-color="#d8d2c6"/><stop offset="1" stop-color="#3b3f78"/>
      </linearGradient>
      <linearGradient id="tone-light" x1="0" y1="0" x2="1" y2="1">
        <stop offset="0" stop-color="#c9b48e"/><stop offset="1" stop-color="#f1dccb"/>
      </linearGradient>
    </defs>
    <polygon role="img" aria-label="Photo of two bridesmaids in navy dresses holding a bouquet" points="14,128 140,86 140,218 14,218" fill="url(#tone-navy)"/>
    <polygon role="img" aria-label="Photo of mascara being applied to a client" points="146,84 268,44 268,190 146,218" fill="url(#tone-skin)"/>
    <polygon role="img" aria-label="Photo of two smiling bridesmaids with finished makeup" points="274,42 396,8 396,160 274,188" fill="url(#tone-party)"/>
    <polygon role="img" aria-label="Photo of makeup being applied to a client's lips" points="402,6 526,6 526,130 402,158" fill="url(#tone-light)"/>
  </svg>

  <p class="services">
    Bridal makeup • Airbrush makeup • Special occasion • Formals<br>
    • Hens nights/ Girls night • Makeup lesson • Makeup for all ages from flower<br>
    girl to Nanna of the bride! • Photoshoot makeup • SPFX
  </p>
</section>

</body>
</html>
```